Business Card for my New Brokerage

Looking to get a business card design for my new Real Estate Brokerage.
I want it with Picture, Phone Number, Email, Website, Office Address
Name and Designation. Please add logo too.

Target Market(s)

Real Estate Investors or Home Buyers

Industry/Entity Type

Real Estate

Contact Information for Business Card

Name, Email, Phone Number, website, email, office address

Colors
EB3D1F
EC4F4E
F09395
F8D3D4
FCEDEE

Requirements
Must have
• Minimalistic, Clean, Modern, Photo
Nice to have
• White and Red Colors

```html
<!DOCTYPE html>
<html lang="en">
<head>
<meta charset="utf-8">
<title>Ember Realty Inc — Business Card</title>
<link href="https://fonts.googleapis.com/css2?family=Montserrat:wght@500;800&family=Arimo:wght@400;700&display=swap" rel="stylesheet">
<style>
  :root {
    --backdrop: #2a2a2c;
    --card: #141414;
    --red: #e30613;
    --gold: #b8893c;
    --white: #f2f2f2;
    --grey: #d9d9d9;
    --photo-top: #5a4a42;
    --photo-mid: #3a3534;
    --photo-end: #1e1e20;
  }
  * { margin: 0; padding: 0; box-sizing: border-box; }
  html, body { width: 1200px; height: 1015px; overflow: hidden; }
  body {
    background: var(--backdrop);
    display: flex;
    flex-direction: column;
    align-items: center;
    justify-content: center;
    gap: 44px;
    font-family: "Arimo", Arial, sans-serif;
  }
  .card {
    position: relative;
    width: 820px;
    height: 440px;
    background: var(--card);
    border-top: 3px solid var(--gold);
    overflow: hidden;
    box-shadow: 0 10px 30px rgba(0,0,0,.45);
  }
  .card::after {
    content: "";
    position: absolute;
    left: 0; right: 0; bottom: 0;
    height: 9px;
    background: var(--red);
    z-index: 2;
  }
  .brand {
    font-family: "Montserrat", sans-serif;
    font-weight: 800;
    color: var(--red);
    letter-spacing: 1px;
    display: flex;
    align-items: center;
    gap: 10px;
    white-space: nowrap;
  }
  .brand-mark {
    width: 12px; height: 12px;
    background: var(--red);
    flex: none;
  }
  .card-back .brand {
    position: absolute;
    top: 50%; left: 50%;
    transform: translate(-50%, -50%);
    font-size: 52px;
  }
  .card-front .brand {
    position: absolute;
    top: 40px; left: 48px;
    font-size: 34px;
  }
  .agent {
    position: absolute;
    left: 48px; top: 118px;
  }
  .agent-name {
    font-family: "Montserrat", sans-serif;
    font-weight: 800;
    font-size: 30px;
    line-height: 1.2;
    color: var(--red);
    letter-spacing: .5px;
  }
  .agent-title {
    font-size: 21px;
    line-height: 1.25;
    color: var(--white);
    margin-top: 2px;
  }
  .contact {
    list-style: none;
    margin-top: 18px;
  }
  .contact li {
    display: flex;
    align-items: center;
    gap: 12px;
    font-size: 21px;
    color: var(--white);
    line-height: 1.5;
  }
  .contact svg { width: 21px; height: 21px; flex: none; }
  .contact .accent { color: var(--red); }
  .address {
    margin-top: 14px;
    font-size: 21px;
    line-height: 1.4;
    color: var(--grey);
  }
  .agent-photo {
    position: absolute;
    right: 0; top: 60px; bottom: 0;
    width: 310px;
    background: linear-gradient(160deg, var(--photo-top) 0%, var(--photo-mid) 45%, var(--photo-end) 100%);
  }
</style>
</head>
<body>

  <section class="card card-back">
    <div class="brand"><span>EMBER REALTY INC</span><span class="brand-mark"></span></div>
  </section>

  <section class="card card-front">
    <div class="brand"><span>EMBER REALTY INC</span><span class="brand-mark"></span></div>

    <div class="agent">
      <h1 class="agent-name">MARCUS HALE</h1>
      <p class="agent-title">Managing Director</p>

      <ul class="contact">
        <li>
          <svg viewBox="0 0 24 24" aria-hidden="true"><path fill="var(--red)" d="M6.6 10.8a15.1 15.1 0 0 0 6.6 6.6l2.2-2.2a1 1 0 0 1 1-.25 11.4 11.4 0 0 0 3.6.57 1 1 0 0 1 1 1V20a1 1 0 0 1-1 1A17 17 0 0 1 3 4a1 1 0 0 1 1-1h3.5a1 1 0 0 1 1 1c0 1.25.2 2.45.57 3.57a1 1 0 0 1-.25 1z"/></svg>
          <span>020-555 018 642</span>
        </li>
        <li>
          <svg viewBox="0 0 24 24" aria-hidden="true"><rect x="2" y="5" width="20" height="14" fill="var(--red)"/><path d="M2 5l10 8 10-8" fill="none" stroke="var(--card)" stroke-width="1.6"/></svg>
          <span>hello@emberrealty.com</span>
        </li>
        <li>
          <svg viewBox="0 0 24 24" aria-hidden="true"><g fill="none" stroke="var(--red)" stroke-width="2"><circle cx="12" cy="12" r="9"/><ellipse cx="12" cy="12" rx="4" ry="9"/><path d="M3 12h18M5 7h14M5 17h14"/></g></svg>
          <span>www.<span class="accent">emberrealty</span>.com</span>
        </li>
      </ul>

      <p class="address">18 Harbour Lane, Suite 4<br>Westfield 30218</p>
    </div>

    <div class="agent-photo" role="img" aria-label="Portrait photo of the agent in a dark suit and tie"></div>
  </section>

</body>
</html>
```